VELORA SPORTS NETWORK

design a website that will be a companion to a sports network that features womens sports and fitness content.
With the goal of promoting and empowering female athleticism, Velorabx.example will be the online network that connects female sports fans to the sports they love and follow. The site aims to raise the level of awareness of women in sports by providing comprehensive sports coverage, spotlighting outstanding achievements, and working with sporting associations on advocacy issues and empowering programs.
Updates
I would like to have all entry by Sunday June 8 2014 thank you
please use actual script not lorem ipsum
thank you
Deadline winding down, added new pictures to file
Target Market(s)
our target market is females 18-54, whom love womens sports and ftiness
Industry/Entity Type
Fitness
Font styles to use
Requirements
Must have
- Attributes of the website:
1. Large Photos: to accompany current stories
2. Colorful: Highlight Velora’s officials colors
3. News Area: recent news items on the home page and achieved news stories
4. Featured Content area: Headline news, athlete spotlights and issues
5. Streaming content: to accompany news and featured content
6. Advertiser links: to purchase merchandise
7. Real-time scores of live events
8. Blog
9. Monthly newsletter
10. Athlete profile page
11. Model close to KVRM
Nice to have
- Velorabx.example will offer value-added service that will entitle customers to gain access to online streaming services provided by Velora, which delivers both live streams and on-demand replays of global women’s sports events to sports fans in U.S. and abroad. This service will be subscription based for a modest monthly fee. Content will be available across multiple platforms and cloud based. New subscriber will get first 30 days free.
Content will include:
1. Live sports events
2. On-demand and premium content
3. Fan-generated Content

```html
<!DOCTYPE html>
<html lang="en">
<head>
<meta charset="utf-8">
<title>Velora Sports Network</title>
<link rel="stylesheet" href="https://fonts.googleapis.com/css2?family=Open+Sans:wght@400;600;700&family=Roboto+Condensed:wght@400;700&display=swap">
<style>
:root{
  --red:#d8322b;
  --red-dark:#b3241e;
  --ink:#333333;
  --muted:#777777;
  --line:#dddddd;
  --panel:#ececec;
  --dark:#2e2e2e;
  --white:#ffffff;
}
*{box-sizing:border-box;margin:0;padding:0}
html,body{width:1200px;height:2304px;overflow:hidden}
body{font-family:"Open Sans",Arial,sans-serif;color:var(--ink);background:#f2f2f2;font-size:12px}
.page-top{background:var(--white)}
.wrap{width:1056px;margin:0 auto;position:relative}
a{color:inherit;text-decoration:none}

/* header */
.site-header{height:120px}
.brand{position:absolute;left:0;top:18px;display:flex;align-items:center;gap:12px}
.brand-dot{width:62px;height:62px;border-radius:50%;background:var(--red)}
.brand-name{font-family:"Roboto Condensed",sans-serif;font-weight:700;font-size:26px;color:var(--red);letter-spacing:1px}
.utility{position:absolute;right:0;top:14px;display:flex;align-items:center;gap:10px;font-size:11px;color:var(--red)}
.utility .sep{color:var(--line)}
.search{width:120px;height:22px;border:1px solid var(--line);border-radius:2px;margin-left:8px}
.main-nav{position:absolute;right:0;top:66px;display:flex}
.main-nav a{font-family:"Roboto Condensed",sans-serif;font-size:14px;font-weight:700;color:var(--red);padding:12px 16px;text-transform:uppercase}
.main-nav a.active{background:var(--red);color:var(--white)}

/* hero */
.hero{height:540px;position:relative}
.hero-photo{position:absolute;inset:0 72px;background:linear-gradient(160deg,#3d6a8a 0%,#9fb0a8 35%,#5d7b3e 70%,#2f4a22 100%)}
.hero-caption{position:absolute;left:72px;right:72px;bottom:60px;height:120px;background:rgba(20,20,20,.72);padding:18px 24px;color:var(--white)}
.hero-caption h1{font-size:28px;font-weight:600;margin-bottom:8px}
.hero-caption p{font-size:12px;color:#ddd;width:700px;line-height:1.5}
.hero-caption .more{display:inline-block;margin-top:6px;color:var(--red);font-weight:700;font-size:11px}
.hero-arrows{position:absolute;right:24px;bottom:24px;display:flex;gap:4px}
.hero-arrows span{width:30px;height:30px;background:rgba(0,0,0,.6);display:flex;align-items:center;justify-content:center}
.hero-dots{position:absolute;left:50%;bottom:30px;transform:translateX(-50%);display:flex;gap:6px}
.hero-dots i{width:8px;height:8px;border-radius:50%;background:#ddd}
.hero-dots i.on{background:var(--red)}

/* scores */
.scores{height:80px;padding-top:12px}
.scores .wrap{height:56px;background:var(--panel);display:flex;align-items:center}
.scores-label{width:140px;height:56px;background:var(--dark);color:var(--white);font-family:"Roboto Condensed",sans-serif;font-weight:700;font-size:14px;text-align:center;padding-top:10px;line-height:1.3}
.scores-select{margin:0 16px;border:2px solid var(--red);background:var(--white);height:30px;padding:0 10px;display:flex;align-items:center;gap:8px;font-weight:700;font-size:11px}
.score-cell{flex:1;border-left:1px solid #cfcfcf;padding:0 14px;font-size:11px;line-height:1.8}
.score-cell b{color:var(--red)}
.scores-arrows{display:flex;gap:2px;padding:0 10px}
.scores-arrows span{width:24px;height:30px;background:var(--red);display:flex;align-items:center;justify-content:center}

/* welcome */
.welcome{height:310px;padding-top:26px}
.welcome .wrap{display:flex;justify-content:space-between}
.welcome-text{width:640px}
.welcome-text h2{font-size:34px;font-weight:400;margin-bottom:14px}
.welcome-text h2 span{color:var(--red)}
.welcome-text p{font-size:12px;line-height:1.7;color:var(--muted);margin-bottom:12px}
.welcome-text h3{font-size:12px;font-weight:700;margin-bottom:4px}
.welcome-text ol{padding-left:18px;color:var(--red);line-height:1.8;font-size:12px}
.welcome-photo{width:380px;height:236px;background:linear-gradient(135deg,#7b8ba5,#c94a3a 55%,#6b8a4a)}

/* news + videos */
.feeds{height:470px}
.feeds .wrap{height:450px;background:var(--panel);padding:16px;display:flex;gap:16px}
.panel{background:var(--white)}
.panel-head{height:36px;background:var(--red);color:var(--white);font-family:"Roboto Condensed",sans-serif;font-weight:700;font-size:15px;display:flex;align-items:center;justify-content:space-between;padding:0 14px}
.panel-head .dots{letter-spacing:2px}
.recent{width:330px}
.news-item{display:flex;gap:12px;padding:12px 14px;border-bottom:1px solid var(--line)}
.news-thumb{width:72px;height:56px;flex:none;background:linear-gradient(135deg,#8a9bb0,#b5543f)}
.news-item p{color:var(--red);font-size:11px;line-height:1.4}
.news-item small{display:block;color:var(--muted);font-size:10px;margin-top:4px}
.read-all{display:block;text-align:right;padding:10px 14px;font-size:10px;font-weight:700;color:var(--muted)}
.videos{flex:1}
.video-body{display:flex;gap:14px;padding:14px}
.video-main{width:400px;height:300px;position:relative;background:linear-gradient(150deg,#4f7a3b,#a8b56f 45%,#3e5c2b)}
.video-main .play{position:absolute;left:50%;top:50%;transform:translate(-50%,-50%)}
.video-main .nav-l,.video-main .nav-r{position:absolute;top:130px;width:26px;height:40px;background:rgba(0,0,0,.5);display:flex;align-items:center;justify-content:center}
.video-main .nav-l{left:0}.video-main .nav-r{right:0}
.video-caption{font-size:11px;color:var(--red);margin-top:8px;width:400px}
.video-caption small{display:block;color:var(--muted);font-size:10px;margin-top:2px}
.video-list{flex:1}
.video-list .news-item{padding:8px 0}

/* headline */
.headline{height:310px;padding-top:10px}
.headline .wrap{display:flex;gap:20px}
.headline-main{flex:1}
.section-title{display:flex;align-items:center;gap:12px;margin-bottom:14px}
.section-title h2{font-family:"Roboto Condensed",sans-serif;font-size:17px;font-weight:700;color:var(--red);white-space:nowrap}
.section-title .rule{flex:1;height:1px;background:var(--line)}
.section-title .dots{color:var(--red);letter-spacing:2px;font-weight:700}
.cards{display:flex;gap:16px}
.card{flex:1}
.card-photo{height:130px;margin-bottom:10px}
.card-photo.one{background:linear-gradient(135deg,#5d7fa8,#c8c0b0)}
.card-photo.two{background:linear-gradient(135deg,#6f8f52,#d9d2c2)}
.card-photo.three{background:linear-gradient(135deg,#3f6f9a,#9fb6c8)}
.card p{color:var(--red);font-size:12px;line-height:1.4}
.card small{display:block;color:var(--muted);font-size:11px;line-height:1.5;margin-top:6px}
.advert{width:250px}
.ad-box{height:210px;background:linear-gradient(160deg,#1f4c8f,#2d77c5 55%,#f0c419)}

/* red band */
.red-band{height:250px;background:var(--red);color:var(--white);padding-top:26px}
.red-band .wrap{display:flex;gap:40px}
.band-col{flex:1}
.band-title{display:flex;align-items:center;gap:12px;margin-bottom:14px}
.band-title h2{font-family:"Roboto Condensed",sans-serif;font-size:17px;font-weight:700;white-space:nowrap}
.band-title .rule{flex:1;height:1px;background:rgba(255,255,255,.5)}
.band-title .dots{letter-spacing:2px;font-weight:700}
.post{margin-bottom:14px}
.post p{font-size:12px;font-weight:600;line-height:1.4}
.post small{display:block;font-size:11px;opacity:.85;line-height:1.5;margin-top:4px}
.newsletter p{font-size:12px;line-height:1.6;margin-bottom:16px;opacity:.92}
.subscribe{display:flex}
.subscribe span{flex:1;height:38px;background:var(--white)}
.subscribe b{background:var(--dark);font-size:12px;padding:0 20px;display:flex;align-items:center}

/* footer */
.site-footer{height:224px;background:#f2f2f2;padding-top:26px}
.site-footer .wrap{display:flex;gap:40px}
.foot-col h4{font-family:"Roboto Condensed",sans-serif;color:var(--red);font-size:13px;margin-bottom:8px}
.foot-col ul{list-style:none;font-size:11px;line-height:1.75;color:var(--muted)}
.foot-col .split{display:flex;gap:40px}
.social li{display:flex;align-items:center;gap:8px}
.social i{width:12px;height:12px;border-radius:50%;background:var(--red);display:inline-block}
.foot-brand{margin-left:auto;text-align:left}
.foot-brand .brand-line{display:flex;align-items:center;gap:10px;margin-bottom:10px}
.foot-brand .brand-dot{width:44px;height:44px}
.foot-brand .brand-name{font-size:20px}
.foot-brand p{font-size:10px;color:var(--muted);line-height:1.6}
</style>
</head>
<body>

<div class="page-top">
<header class="site-header">
  <div class="wrap">
    <div class="brand"><span class="brand-dot"></span><span class="brand-name">VELORA</span></div>
    <div class="utility">
      <a href="#">Log In</a><span class="sep">|</span><a href="#">Help</a><span class="sep">|</span><a href="#">FAQ</a><span class="sep">|</span><a href="#">Blog</a><span class="sep">|</span><a href="#">Site map</a>
      <span class="search"></span>
    </div>
    <nav class="main-nav">
      <a href="#" class="active">Home</a><a href="#">About us</a><a href="#">Sports</a><a href="#">News</a><a href="#">Blog</a><a href="#">Video</a><a href="#">Advertise</a><a href="#">More</a>
    </nav>
  </div>
</header>

<section class="hero">
  <div class="hero-photo" role="img" aria-label="Large action photo of a women's rugby match on a stadium pitch"></div>
  <div class="hero-caption">
    <h1>Lorem ipsum dolor sit amet, consectetur adipisicing</h1>
    <p>Aliquam mollis, nisi et commodo sagittis, eros mi tincidunt nunc, sit amet lacinia lacus nisi sed ullamcorper felis, suspendisse sagittis sapien id libero gravida.</p>
    <a class="more" href="#">READ MORE »</a>
    <div class="hero-arrows">
      <span><svg width="10" height="14" viewBox="0 0 10 14"><path d="M8 1 2 7l6 6" stroke="#fff" stroke-width="2" fill="none"/></svg></span>
      <span><svg width="10" height="14" viewBox="0 0 10 14"><path d="m2 1 6 6-6 6" stroke="#fff" stroke-width="2" fill="none"/></svg></span>
    </div>
  </div>
  <div class="hero-dots"><i class="on"></i><i></i><i></i><i></i></div>
</section>

<section class="scores">
  <div class="wrap">
    <div class="scores-label">REAL-TIME<br>SCORES</div>
    <div class="scores-select">UCSA SCORES <svg width="10" height="6" viewBox="0 0 10 6"><path d="M0 0h10L5 6z" fill="#d8322b"/></svg></div>
    <div class="score-cell"><b>UCSA</b> &nbsp;0 &nbsp;– &nbsp;0<br>LAST 0 &nbsp;·&nbsp; FINAL</div>
    <div class="score-cell"><b>UCSA</b> &nbsp;0 &nbsp;– &nbsp;0<br>LAST 0 &nbsp;·&nbsp; FINAL</div>
    <div class="score-cell"><b>UCSA</b> &nbsp;0 &nbsp;– &nbsp;0<br>LAST 0 &nbsp;·&nbsp; FINAL</div>
    <div class="score-cell"><b>UCSA</b> &nbsp;0 &nbsp;– &nbsp;0<br>LAST 0 &nbsp;·&nbsp; FINAL</div>
    <div class="scores-arrows">
      <span><svg width="8" height="12" viewBox="0 0 8 12"><path d="M6 1 2 6l4 5" stroke="#fff" stroke-width="2" fill="none"/></svg></span>
      <span><svg width="8" height="12" viewBox="0 0 8 12"><path d="m2 1 4 5-4 5" stroke="#fff" stroke-width="2" fill="none"/></svg></span>
    </div>
  </div>
</section>

<section class="welcome">
  <div class="wrap">
    <div class="welcome-text">
      <h2>Welcome to <span>Veloratv</span></h2>
      <p>Velorabx.example will offer value-added service that will entitle customers to gain access to online streaming services provided by Velora, which delivers both live streams and on-demand replays of global women's sports events to sports fans in U.S. and abroad. This service will be subscription based for a modest monthly fee. Content will be available across multiple platforms and cloud based. New subscriber will get first 30 days free.</p>
      <h3>Content will include:</h3>
      <ol>
        <li>Live sports events</li>
        <li>On-demand and premium content</li>
        <li>Fan-generated Content</li>
      </ol>
    </div>
    <div class="welcome-photo" role="img" aria-label="Photo of women soccer players contesting the ball"></div>
  </div>
</section>

<section class="feeds">
  <div class="wrap">
    <div class="panel recent">
      <div class="panel-head">RECENT NEWS <span class="dots">•••</span></div>
      <div class="news-item"><div class="news-thumb" role="img" aria-label="News thumbnail photo"></div><div><p>Season opener draws a record home crowd for the league</p><small>VSN | June 2, 2014, 6:30 pm</small></div></div>
      <div class="news-item"><div class="news-thumb" role="img" aria-label="News thumbnail photo"></div><div><p>Captain signs a new deal and stays with her club</p><small>VSN | June 2, 2014, 6:30 pm</small></div></div>
      <div class="news-item"><div class="news-thumb" role="img" aria-label="News thumbnail photo"></div><div><p>Young sprinter sets a national junior best at relays</p><small>VSN | June 2, 2014, 6:30 pm</small></div></div>
      <div class="news-item"><div class="news-thumb" role="img" aria-label="News thumbnail photo"></div><div><p>Coaches name the final roster for the summer tour</p><small>VSN | June 2, 2014, 6:30 pm</small></div></div>
      <a class="read-all" href="#">READ ALL NEWS »</a>
    </div>
    <div class="panel videos">
      <div class="panel-head">LATEST VIDEOS <span class="dots">•••</span></div>
      <div class="video-body">
        <div>
          <div class="video-main" role="img" aria-label="Video still of a women's football match">
            <span class="nav-l"><svg width="8" height="12" viewBox="0 0 8 12"><path d="M6 1 2 6l4 5" stroke="#fff" stroke-width="2" fill="none"/></svg></span>
            <svg class="play" width="60" height="60" viewBox="0 0 60 60"><circle cx="30" cy="30" r="28" fill="rgba(0,0,0,.55)" stroke="#fff" stroke-width="2"/><path d="M24 18v24l18-12z" fill="#fff"/></svg>
            <span class="nav-r"><svg width="8" height="12" viewBox="0 0 8 12"><path d="m2 1 4 5-4 5" stroke="#fff" stroke-width="2" fill="none"/></svg></span>
          </div>
          <div class="video-caption">Highlights: late goal seals the cup semifinal win<small>June 2, 2014 | 1:55 min</small></div>
        </div>
        <div class="video-list">
          <div class="news-item"><div class="news-thumb" role="img" aria-label="Video thumbnail"></div><div><p>Top five saves from the weekend games</p><small>June 2, 2014</small></div></div>
          <div class="news-item"><div class="news-thumb" role="img" aria-label="Video thumbnail"></div><div><p>Inside the locker room before the final</p><small>June 2, 2014</small></div></div>
          <div class="news-item"><div class="news-thumb" role="img" aria-label="Video thumbnail"></div><div><p>Training day with the national relay team</p><small>June 2, 2014</small></div></div>
          <div class="news-item"><div class="news-thumb" role="img" aria-label="Video thumbnail"></div><div><p>Fan cam: best moments from the stands</p><small>June 2, 2014</small></div></div>
        </div>
      </div>
    </div>
  </div>
</section>

<section class="headline">
  <div class="wrap">
    <div class="headline-main">
      <div class="section-title"><h2>HEADLINE NEWS</h2><span class="rule"></span><span class="dots">•••</span></div>
      <div class="cards">
        <div class="card"><div class="card-photo one" role="img" aria-label="Photo of a softball player at bat"></div><p>Rising star leads her team into the national finals</p><small>A look at the season that made her one of the names to watch.</small></div>
        <div class="card"><div class="card-photo two" role="img" aria-label="Photo of a golfer on the course"></div><p>Veteran golfer claims her third title of the year</p><small>Steady play on the back nine earned a two-stroke victory.</small></div>
        <div class="card"><div class="card-photo three" role="img" aria-label="Photo of swimmers in a pool"></div><p>Swim squad breaks the relay record at home meet</p><small>Four swimmers shaved a full second off the old mark.</small></div>
      </div>
    </div>
    <aside class="advert">
      <div class="section-title"><h2>ADVERTISE WITH US</h2><span class="rule"></span></div>
      <div class="ad-box" role="img" aria-label="Advertising banner promoting live soccer streaming"></div>
    </aside>
  </div>
</section>
</div>

<section class="red-band">
  <div class="wrap">
    <div class="band-col">
      <div class="band-title"><h2>BLOG POST</h2><span class="rule"></span><span class="dots">•••</span></div>
      <div class="post"><p>Why equal coverage matters for the next generation</p><small>Our editors share what visibility means for young athletes and the fans who follow them.</small></div>
      <div class="post"><p>Five training habits from pro athletes you can try</p><small>Simple routines to build strength, speed and focus at any level.</small></div>
    </div>
    <div class="band-col">
      <div class="band-title"><h2>MONTHLY NEWSLETTER</h2><span class="rule"></span><span class="dots">•••</span></div>
      <div class="newsletter">
        <p>Get the month's top stories, athlete spotlights and live event dates sent straight to your inbox. Sign up today and never miss a game.</p>
        <div class="subscribe"><span></span><b>SUBSCRIBE NOW</b></div>
      </div>
    </div>
  </div>
</section>

<footer class="site-footer">
  <div class="wrap">
    <div class="foot-col">
      <h4>SPORTS</h4>
      <div class="split">
        <ul><li>Baseball</li><li>Basketball</li><li>Cheerleaders</li><li>Cross Country</li><li>Fastpitch Softball</li></ul>
        <ul><li>Field Hockey</li><li>Football</li><li>Golf</li><li>Gymnastics</li><li>Lacrosse</li></ul>
        <ul><li>LetGlory</li><li>Slowpitch Softball</li><li>Soccer</li><li>Track &amp; Field</li><li>Volleyball</li></ul>
      </div>
    </div>
    <div class="foot-col">
      <h4>HELP</h4>
      <ul><li>Contact Us</li><li>FAQ</li></ul>
    </div>
    <div class="foot-col">
      <h4>CONNECT US</h4>
      <ul class="social"><li><i></i>Friendly</li><li><i></i>Chirper</li><li><i></i>Rss</li><li><i></i>ViewTube</li></ul>
    </div>
    <div class="foot-brand">
      <div class="brand-line"><span class="brand-dot"></span><span class="brand-name">VELORA</span></div>
      <p>Copyright © 2014. All Rights<br>Reserved.</p>
    </div>
  </div>
</footer>

</body>
</html>
```